Business Card Design Project : Ridgeline Press

In preparation for market launch, Tamarind's Ridgeline Press require the development of a business card. Ridgeline Press is a Community online publishing web portal. We provide the the city of Whistler located in B.C. (Canada) business directories, News, Classified ads, News, Events and blogs etc.

The main focus of the brand is to help local businesses to corporate with their online advertisement and marketing. Meeting our clients face to face is a must (B2B).

Target Market(s)

The target market is B2B customers. Business Owners to Marketing, advertising Managers

Industry/Entity Type

Business

Requirements
Must have
• - The business card will be two sided.
the BACK side will have our logo which consist of (icon, url,slogan) submited. The logo will be middle and centred.

The FRONT side should have company details:

Company Legal Name: TAMARIND RIDGELINE MEDIA

Owen Farsk
Director of Sales & Marketing

www.tamarindridgeline.biz
owen@tamarindridgeline.biz

Phone: 604 317 8842
#2714 - 582 E. Halvern St.
Vancouver, B.C. V7K2R4 Canada
Nice to have
• - For the "FRONT" side of our business card. You can separate or re-arrange with our logo components (icon, logo,slogan). It does not have to be together.

Also our company legal name is rather long so arrange or organize the name in a way to make it shorter. Your experience and creativity will have to come in play.
Should not have
• should not have other colors beside logo color and black text (2 colors). Also nothing Three dimensional

```html
<!DOCTYPE html>
<html lang="en">
<head>
<meta charset="utf-8">
<title>Tamarind Ridgeline Media – Business Card</title>
<link href="https://fonts.googleapis.com/css2?family=Source+Sans+3:wght@400;600;700&display=swap" rel="stylesheet">
<style>
  :root {
    --brand-blue: #2479c2;
    --ink: #111111;
    --band-black: #0b0b0c;
    --card-white: #ffffff;
    --backdrop: #ececec;
    --on-dark: #ffffff;
  }
  * { margin: 0; padding: 0; box-sizing: border-box; }
  html, body {
    width: 1200px; height: 900px; overflow: hidden;
    background: var(--backdrop);
    font-family: "Source Sans 3", "Myriad Pro", sans-serif;
  }
  .canvas { position: relative; width: 1200px; height: 900px; }

  .card {
    position: absolute;
    background: var(--card-white);
    border-radius: 28px;
    overflow: hidden;
    border: 1px solid #dcdcdc;
  }

  /* ---------- Back side ---------- */
  .card--back { left: 93px; top: 52px; width: 591px; height: 370px; }
  .card--back .company-name {
    position: absolute; left: 0; right: 0; top: 178px;
    text-align: center; font-weight: 700; font-size: 27px;
    color: var(--ink); letter-spacing: -0.2px;
  }
  .card--back .slogan {
    position: absolute; left: 0; right: 0; top: 217px;
    text-align: center; font-size: 20px; color: var(--brand-blue);
  }
  .url-band {
    position: absolute; right: 0; bottom: 0; height: 41px;
    background: var(--brand-blue);
    color: var(--on-dark); font-size: 15.5px;
    display: flex; align-items: center; justify-content: flex-end;
    padding-right: 18px;
  }
  .card--back .url-band {
    width: 254px;
    clip-path: polygon(32px 0, 100% 0, 100% 100%, 0 100%);
  }

  /* ---------- Front side ---------- */
  .card--front { left: 459px; top: 449px; width: 613px; height: 369px; }
  .card--front .brand-block {
    position: absolute; right: 44px; top: 106px; text-align: center;
  }
  .card--front .company-name {
    font-weight: 700; font-size: 20.5px; color: var(--ink); line-height: 1.1;
  }
  .card--front .slogan {
    font-size: 17px; color: var(--brand-blue); margin-top: 3px;
  }
  .person { position: absolute; left: 130px; top: 218px; }
  .person__name { font-weight: 700; font-size: 19px; color: var(--ink); line-height: 1.1; }
  .person__title { font-weight: 600; font-size: 15.5px; color: var(--brand-blue); margin-top: 3px; }

  .contact-stripe {
    position: absolute; left: 0; top: 271px; width: 613px; height: 98px;
    background: var(--brand-blue);
    clip-path: polygon(116px 0, 130px 0, 33px 100%, 19px 100%);
  }
  .contact-band {
    position: absolute; left: 0; top: 271px; width: 613px; height: 98px;
    background: var(--band-black);
    clip-path: polygon(130px 0, 100% 0, 100% 100%, 33px 100%);
  }
  .card--front .url-band {
    width: 267px; height: 46px; font-size: 15.5px; padding-right: 14px;
    clip-path: polygon(44px 0, 100% 0, 100% 100%, 0 100%);
  }
  .contact-list {
    position: absolute; left: 122px; top: 287px; list-style: none;
    color: var(--on-dark); font-size: 15px;
  }
  .contact-list li { display: flex; align-items: center; height: 24px; }
  .contact-list svg { width: 14px; height: 14px; margin-right: 13px; fill: var(--brand-blue); flex: none; }
</style>
</head>
<body>
<main class="canvas">

  <section class="card card--back" aria-label="Business card back">
    <h1 class="company-name">TAMARIND RIDGELINE MEDIA</h1>
    <p class="slogan">Your information gateway</p>
    <div class="url-band">www.tamarindridgeline.biz</div>
  </section>

  <section class="card card--front" aria-label="Business card front">
    <div class="brand-block">
      <p class="company-name">TAMARIND RIDGELINE MEDIA</p>
      <p class="slogan">Your information gateway</p>
    </div>

    <div class="person">
      <p class="person__name">OWEN FARSK</p>
      <p class="person__title">Director of Sales &amp; Marketing</p>
    </div>

    <div class="contact-stripe"></div>
    <div class="contact-band"></div>

    <ul class="contact-list">
      <li>
        <svg viewBox="0 0 14 14" aria-hidden="true"><path d="M7 1 L13.5 7 H11.5 V13 H8.5 V9 H5.5 V13 H2.5 V7 H0.5 Z"/></svg>
        #2714 - 582 E. Halvern St. Vancouver, B.C. V7K2R4 Canada
      </li>
      <li>
        <svg viewBox="0 0 14 14" aria-hidden="true"><path d="M3 1 L5.5 1 L6.5 4.5 L5 5.8 C5.8 7.6 6.6 8.5 8.2 9.2 L9.6 7.6 L13 8.6 L13 11 C13 12.2 12 13 10.8 12.8 C5.8 12 2 8.2 1.2 3.2 C1 2 1.8 1 3 1 Z"/></svg>
        604 317 8842
      </li>
      <li>
        <svg viewBox="0 0 14 14" aria-hidden="true"><path d="M1 3 H13 V4 L7 8 L1 4 Z M1 5.3 L7 9.3 L13 5.3 V11 H1 Z"/></svg>
        owen@tamarindridgeline.biz
      </li>
    </ul>

    <div class="url-band">www.tamarindridgeline.biz</div>
  </section>

</main>
</body>
</html>
```